Harbor Grout Works Business card logo

We are a tile and natural stone installation company with an emphasis on high quality and design assistance. I prefer a black background with a graphic logo or maybe a photo that gives a feel of tile/natural stone. I like bold, but tasteful colors. Something to really catch the eye without being gaudy. The final design should convey expert quality and attention to detail.

Contact Information for Business Card

HARBOR GROUT WORKS Quality Design and Installation

Font styles to use
Other font styles liked:
• Graviton, Illegal curves

Requirements
Must have
• Business card must be an eye-catcher, but tasteful.
• Information I need on the card:
• Business name and tagline
• Dennis Halvorsen, owner
• Phone: (xxx) xxx-xxxx
• Email
• Website

```html
<!DOCTYPE html>
<html lang="en">
<head>
<meta charset="utf-8">
<title>Harbor Grout Works — Business Card</title>
<link rel="stylesheet" href="https://fonts.googleapis.com/css2?family=Michroma&display=swap">
<style>
  :root {
    --backdrop: #0b0b0c;
    --front-card: #141415;
    --front-ink: #e9e9ea;
    --stone-light: #9a9ea1;
    --stone-mid: #7a7e82;
    --stone-dark: #585c60;
    --stone-vein: #6a6e72;
    --stone-ink: #3e4145;
    --stone-line: #4a4d51;
  }
  html, body {
    margin: 0;
    width: 1200px;
    height: 871px;
    overflow: hidden;
    background: var(--backdrop);
  }
  .canvas {
    position: relative;
    width: 1200px;
    height: 871px;
    font-family: "Michroma", sans-serif;
  }
  .card {
    position: absolute;
    left: 310px;
    width: 580px;
    height: 331px;
    border-radius: 3px;
    overflow: hidden;
  }
  .card-front {
    top: 70px;
    background: var(--front-card);
    box-shadow: 0 0 0 1px #222;
  }
  .card-back {
    top: 470px;
  }
  .front-brand {
    position: absolute;
    left: 0; right: 0;
    top: 128px;
    text-align: center;
    color: var(--front-ink);
  }
  .brand-name {
    display: block;
    font-size: 28px;
    letter-spacing: 2px;
    line-height: 1.2;
    white-space: nowrap;
  }
  .brand-tagline {
    display: block;
    margin-top: 12px;
    font-size: 11px;
    letter-spacing: 2.5px;
    text-transform: uppercase;
    white-space: nowrap;
  }
  .stone-surface {
    position: absolute;
    inset: 0;
    background:
      radial-gradient(ellipse 40% 30% at 20% 25%, var(--stone-light), transparent 70%),
      radial-gradient(ellipse 35% 25% at 70% 20%, var(--stone-vein), transparent 70%),
      radial-gradient(ellipse 30% 40% at 45% 80%, var(--stone-dark), transparent 70%),
      radial-gradient(ellipse 45% 35% at 88% 70%, var(--stone-dark), transparent 70%),
      linear-gradient(160deg, var(--stone-mid), var(--stone-dark));
  }
  .back-layout {
    position: absolute;
    inset: 0;
    display: flex;
    align-items: center;
    color: var(--stone-ink);
  }
  .back-brand {
    width: 250px;
    padding-left: 18px;
    padding-right: 14px;
    text-align: right;
    box-sizing: content-box;
  }
  .back-brand .brand-name {
    font-size: 12.5px;
    letter-spacing: 1px;
  }
  .back-brand .brand-tagline {
    font-size: 6.5px;
    letter-spacing: 0.8px;
    margin-top: 8px;
  }
  .back-divider {
    width: 2px;
    height: 120px;
    background: var(--stone-line);
  }
  .contact {
    padding-left: 16px;
  }
  .contact-name {
    font-size: 15px;
    letter-spacing: 1.5px;
    margin: 0;
    white-space: nowrap;
  }
  .contact-role {
    font-size: 9px;
    letter-spacing: 2px;
    margin: 4px 0 12px;
  }
  .contact-list {
    list-style: none;
    margin: 0;
    padding: 0;
    font-size: 11px;
    letter-spacing: 1.5px;
  }
  .contact-list li {
    display: flex;
    align-items: center;
    gap: 8px;
    margin-bottom: 8px;
  }
  .contact-icon {
    width: 13px;
    height: 13px;
    fill: none;
    stroke: var(--stone-ink);
    stroke-width: 1.6;
  }
</style>
</head>
<body>
<main class="canvas">
  <section class="card card-front" aria-label="Business card front">
    <div class="front-brand">
      <span class="brand-name">HARBOR GROUT WORKS</span>
      <span class="brand-tagline">Quality Design and Installation</span>
    </div>
  </section>

  <section class="card card-back" aria-label="Business card back">
    <div class="stone-surface" role="img" aria-label="Grey natural stone texture filling the card"></div>
    <div class="back-layout">
      <div class="back-brand">
        <span class="brand-name">HARBOR GROUT WORKS</span>
        <span class="brand-tagline">Quality Design and Installation</span>
      </div>
      <div class="back-divider"></div>
      <div class="contact">
        <p class="contact-name">DENNIS HALVORSEN</p>
        <p class="contact-role">OWNER</p>
        <ul class="contact-list">
          <li>
            <svg class="contact-icon" viewBox="0 0 14 14" aria-hidden="true"><path d="M2 5 Q7 1 12 5 L10 7 L8.5 5.5 H5.5 L4 7 Z M3 8 H11 V12 H3 Z"/></svg>
            000-000-0000
          </li>
          <li>
            <svg class="contact-icon" viewBox="0 0 14 14" aria-hidden="true"><rect x="1.5" y="3" width="11" height="8"/><path d="M1.5 3 L7 8 L12.5 3"/></svg>
            EMAIL@
          </li>
          <li>
            <svg class="contact-icon" viewBox="0 0 14 14" aria-hidden="true"><circle cx="7" cy="7" r="5.5"/><ellipse cx="7" cy="7" rx="2.3" ry="5.5"/><path d="M1.5 7 H12.5"/></svg>
            WEBSITE
          </li>
        </ul>
      </div>
    </div>
  </section>
</main>
</body>
</html>
```